Vertical Banner

I need an eye-catching banner created for street fairs, indoor and outdoor events to draw attention to our language school. It will be to print on this banner (specs included):
https://www.banvoxprint.com/tag/617/Retractable-Banners/product/5174-46/Economy-Retractor-Banner-Display-27-09

I want the banner to be:
- SIMPLE
- Eye catching (not busy with too many pictures or information)
- It should say at top prominently: "Come learn a language!" and have our name.
- Below these languages should be large and eye-catching: Spanish, Chinese, French, Russian, German, Italian, Farsi, Turkish, Portuguese, ASL, Cantonese, Japanese, Korean, Vietnamese, Arabic, Dutch, more... (if some need to be cut our because of overcrowding let me know OR we can make some big and others small)
- Below this it should have GROUP & PRIVATE LESSONS
- It should be colorful and make people think of things international - perhaps national flags in background? Or images of world famous monuments? Could be image of adutls in a classroom. Sth that gets people excited about travel and language learning
- It should have our contact info VERY large at bottom:
Tovira Languages -
San Francisco, Silicon Valley & New York City
www.toviralanguagesf.com
415-629-5140
info@toviralanguagesf.com
(this can be smaller)
Four Wexmoor Plaza
Lobby 3
San Francisco, CA 94187

Hey Designers, please feel free to do a rough take on it. I don't need you to spend too much time, just give me a general idea of how you would make it look, then i know we can go from there later and refine it. Feel free to make it more of a quick sketch to show how you would do it.

Target Market(s)

adults from about 25-55 years old, educated, employed and typically world travellers

Industry/Entity Type

School

Colors
86cfc6
00a990
cadf82
acd036
9bcb3c
fbed22
f78f20
ffc214
f37122

Requirements
Must have
• Must be simple! Too many banners put way too much information and pictures. I want someone to walk by and immediately know we teach foreign languages. Must have bright colors and large font for languages offered
Should not have
• Should not be too full of images and design that distract the viewer from seeing the main thing I want them to see: that we teacher languages

```html
<!DOCTYPE html>
<html lang="en">
<head>
<meta charset="utf-8">
<title>Tovira Languages – Vertical Banner</title>
<link rel="stylesheet" href="https://fonts.googleapis.com/css2?family=Anton&family=Roboto+Condensed:wght@400;700&family=Lobster&display=swap">
<style>
  :root {
    --page-bg: #e4e6e8;
    --white: #ffffff;
    --brand-green: #00843d;
    --headline-red: #e3161b;
    --headline-yellow: #fff200;
    --divider-red: #e3161b;
    --ribbon-red: #e3161b;
    --ribbon-yellow: #fff200;
    --footer-green: #00843d;
    --ink-dark: #1f1f1f;
    --photo-light: #eef1f4;
    --photo-mid: #c9ced6;
  }
  * { box-sizing: border-box; margin: 0; padding: 0; }
  html, body { width: 1200px; height: 1175px; overflow: hidden; }
  body {
    background: var(--page-bg);
    display: flex;
    align-items: center;
    justify-content: center;
    font-family: "Roboto Condensed", "Arial Narrow", sans-serif;
  }
  .banner {
    width: 420px;
    height: 1135px;
    background: var(--white);
    display: flex;
    flex-direction: column;
    box-shadow: 0 6px 20px rgba(0,0,0,0.15);
    overflow: hidden;
  }
  .brand {
    height: 205px;
    display: flex;
    align-items: center;
    justify-content: center;
    gap: 12px;
  }
  .brand-dot {
    width: 22px; height: 22px; border-radius: 50%;
    background: var(--brand-green);
  }
  .brand-name {
    font-family: "Roboto Condensed", "Arial Narrow", sans-serif;
    font-weight: 700;
    font-size: 52px;
    color: var(--brand-green);
    letter-spacing: 0.5px;
  }
  .headline-band {
    position: relative;
    height: 195px;
    background: var(--headline-red);
    clip-path: polygon(0 0, 100% 12px, 100% 100%, 0 100%);
    display: flex;
    flex-direction: column;
    align-items: center;
    justify-content: center;
    padding-top: 10px;
  }
  .headline-band::before {
    content: "";
    position: absolute; top: 0; left: 0; right: 0; height: 5px;
    background: linear-gradient(90deg, var(--brand-green) 0 45%, var(--headline-yellow) 45% 100%);
  }
  .headline {
    font-family: "Anton", "Impact", sans-serif;
    color: var(--headline-yellow);
    text-transform: uppercase;
    line-height: 0.98;
    text-align: center;
  }
  .headline-top { font-size: 66px; display: block; }
  .headline-bottom { font-size: 82px; display: block; }
  .languages {
    height: 190px;
    display: flex;
    flex-direction: column;
    justify-content: center;
    align-items: center;
    gap: 6px;
    padding-top: 6px;
  }
  .language-row {
    font-weight: 700;
    font-size: 23px;
    color: var(--brand-green);
    white-space: nowrap;
  }
  .language-row .sep { color: var(--divider-red); font-weight: 400; margin: 0 5px; }
  .lessons-ribbon {
    height: 80px;
    position: relative;
    display: flex;
    align-items: center;
    justify-content: center;
  }
  .lessons-ribbon svg { position: absolute; inset: 0; }
  .lessons-title {
    position: relative;
    font-family: "Lobster", cursive;
    font-size: 31px;
    color: var(--ribbon-yellow);
    transform: rotate(-2deg);
  }
  .photo {
    height: 270px;
    background: radial-gradient(ellipse at 55% 60%, var(--photo-mid), var(--photo-light) 70%);
  }
  .contact {
    flex: 1;
    background: var(--footer-green);
    color: var(--white);
    display: flex;
    flex-direction: column;
    align-items: center;
    justify-content: center;
    gap: 4px;
    text-align: center;
  }
  .contact-cities { font-weight: 700; font-size: 19px; }
  .contact-line { display: flex; gap: 14px; align-items: center; font-weight: 700; font-size: 18px; }
  .contact-item { display: inline-flex; align-items: center; gap: 5px; }
  .contact-item svg { width: 14px; height: 14px; }
  .contact-email { font-size: 16px; font-weight: 400; }
  .contact-address { font-weight: 700; font-size: 20px; line-height: 1.15; margin-top: 2px; }
</style>
</head>
<body>
  <main class="banner">
    <header class="brand">
      <span class="brand-dot"></span>
      <span class="brand-name">Tovira Languages</span>
    </header>

    <section class="headline-band">
      <h1 class="headline">
        <span class="headline-top">Come learn a</span>
        <span class="headline-bottom">Language!</span>
      </h1>
    </section>

    <section class="languages" aria-label="Languages offered">
      <p class="language-row">Spanish<span class="sep">|</span>Chinese<span class="sep">|</span>French<span class="sep">|</span>Russian</p>
      <p class="language-row">German<span class="sep">|</span>Italian<span class="sep">|</span>Farsi<span class="sep">|</span>Turkish<span class="sep">|</span>ASL</p>
      <p class="language-row">Portuguese<span class="sep">|</span>Cantonese<span class="sep">|</span>Japanese</p>
      <p class="language-row">Korean<span class="sep">|</span>Arabic<span class="sep">|</span>Dutch</p>
      <p class="language-row">Vietnamese<span class="sep">|</span>more...</p>
    </section>

    <section class="lessons-ribbon">
      <svg viewBox="0 0 420 80" preserveAspectRatio="none" aria-hidden="true">
        <polygon points="28,16 396,8 384,40 398,64 30,72 42,44" fill="var(--ribbon-yellow)"/>
        <polygon points="22,22 392,14 378,42 394,60 24,68 38,44" fill="var(--ribbon-red)"/>
      </svg>
      <h2 class="lessons-title">Group &amp; Private Lessons</h2>
    </section>

    <div class="photo" role="img" aria-label="Photo of smiling young adults holding small national flags of many countries"></div>

    <footer class="contact">
      <p class="contact-cities">San Francisco, Silicon Valley &amp; New York City</p>
      <p class="contact-line">
        <span class="contact-item">
          <svg viewBox="0 0 16 16" aria-hidden="true"><circle cx="8" cy="8" r="8" fill="#fff"/><path d="M5 4.5l1.6-.5 1 2.2-1 .8a5 5 0 0 0 2.4 2.4l.8-1 2.2 1-.5 1.6c-3.5.4-6.9-3-6.5-6.5z" fill="var(--footer-green)"/></svg>
          415-629-5140
        </span>
        <span class="contact-item">
          <svg viewBox="0 0 16 16" aria-hidden="true" fill="none" stroke="#fff" stroke-width="1.3"><circle cx="8" cy="8" r="6.5"/><ellipse cx="8" cy="8" rx="3" ry="6.5"/><path d="M1.5 8h13"/></svg>
          www.toviralanguagesf.com
        </span>
      </p>
      <p class="contact-line contact-email">
        <span class="contact-item">
          <svg viewBox="0 0 16 16" aria-hidden="true" fill="none" stroke="#fff" stroke-width="1.3"><circle cx="8" cy="8" r="6.5"/><rect x="4.5" y="5.5" width="7" height="5"/><path d="M4.5 5.5L8 8.5l3.5-3"/></svg>
          info@toviralanguagesf.com
        </span>
      </p>
      <p class="contact-address">Four Wexmoor Plaza, Lobby 3<br>San Francisco, CA 94187</p>
    </footer>
  </main>
</body>
</html>
```